U.S. Popcorn company needs business cards

We are a popcorn company that manufactures popcorn and sells it to grocery stores worldwide. Our theme is "Americana" and our logo is U.S. route 66 which is the most famous highway in the U.S.

We would like the design to be simple and to use both sides. On the back side we would like to see just the logo and website. The front would be normal details

Target Market(s)

Wholesalers, grocers and distributors

Industry/Entity Type

Manufacture

Contact Information for Business Card

Business name: Prairie Lantern Popcorn
Phone: +1 555 308 4726
Email: Dale@prairielanternpopcorn.com
website: www.prairielanternpopcorn.com
Tag Line: "POPular for a reason"
Name: Dale Whitcombe
Title: Founder/President

Requirements
Must have
• Either this design should be fun or clean and simple. I will let you show me your thougths.
Nice to have
• Anything that ties in the real Hwy Route 66.
• Colors might need to be red, white and blue incorporated.
Should not have
• Not be too busy.

```html
<!DOCTYPE html>
<html lang="en">
<head>
<meta charset="utf-8">
<title>Prairie Lantern Popcorn – Business Cards</title>
<link href="https://fonts.googleapis.com/css2?family=Mulish:wght@400;700;800&display=swap" rel="stylesheet">
<style>
  :root {
    --backdrop: #1d1d1f;
    --card-black: #141416;
    --route-red: #e0231f;
    --route-blue: #12306b;
    --ink-white: #f4f4f4;
    --foil-silver: #9a9a9e;
  }
  * { margin: 0; padding: 0; box-sizing: border-box; }
  html, body { width: 1200px; height: 793px; overflow: hidden; }
  body {
    background: var(--backdrop);
    font-family: "Mulish", sans-serif;
    position: relative;
  }
  .card {
    position: absolute;
    width: 525px;
    height: 300px;
    border-radius: 12px;
    background: var(--card-black);
    overflow: hidden;
    box-shadow: 0 10px 30px rgba(0,0,0,.55);
  }
  .card--back { left: 45px; top: 246px; }
  .card--front { left: 630px; top: 246px; }

  .back-mark {
    position: absolute;
    inset: 0;
    display: flex;
    align-items: center;
    justify-content: center;
    gap: 12px;
  }
  .back-mark__dot {
    width: 18px; height: 18px; border-radius: 50%;
    background: var(--foil-silver);
  }
  .back-mark__name {
    font-weight: 800;
    font-size: 26px;
    color: var(--foil-silver);
    letter-spacing: .5px;
  }

  .front-waves { position: absolute; inset: 0; width: 525px; height: 300px; }

  .front-brand {
    position: absolute;
    left: 30px; top: 112px;
    width: 190px;
    display: flex;
    align-items: center;
    gap: 10px;
  }
  .front-brand__dot {
    flex: none;
    width: 16px; height: 16px; border-radius: 50%;
    background: var(--route-red);
  }
  .front-brand__name {
    font-weight: 800;
    font-size: 20px;
    line-height: 1.15;
    color: var(--ink-white);
  }

  .person {
    position: absolute;
    right: 24px; top: 24px;
    text-align: right;
  }
  .person__name {
    font-weight: 800;
    font-size: 24px;
    color: var(--route-red);
    line-height: 1.1;
  }
  .person__title {
    font-size: 12px;
    color: var(--ink-white);
    margin-top: 2px;
  }
  .tagline {
    position: absolute;
    right: 24px; top: 92px;
    font-size: 16px;
    line-height: 20px;
    color: var(--ink-white);
  }
  .tagline strong { font-weight: 800; }

  .contacts {
    position: absolute;
    right: 20px; top: 178px;
    list-style: none;
    text-align: right;
    color: var(--ink-white);
    font-size: 12.5px;
    line-height: 19px;
  }
  .contacts li { display: flex; justify-content: flex-end; align-items: center; gap: 7px; }
  .contacts svg { width: 11px; height: 11px; fill: var(--route-red); flex: none; }
</style>
</head>
<body>

  <section class="card card--back" aria-label="Card back">
    <div class="back-mark">
      <span class="back-mark__dot"></span>
      <span class="back-mark__name">Prairie Lantern Popcorn</span>
    </div>
  </section>

  <section class="card card--front" aria-label="Card front">
    <svg class="front-waves" viewBox="0 0 525 300" aria-hidden="true">
      <path d="M0,265 C150,262 260,250 330,200 C390,155 450,150 525,150 L525,300 L0,300 Z" fill="var(--route-blue)"/>
      <path d="M0,246 C150,244 255,232 320,185 C385,138 450,132 525,132 L525,142 C452,142 392,148 328,195 C262,242 150,255 0,257 Z" fill="var(--route-red)"/>
      <path d="M70,232 C180,230 260,215 310,180 C265,220 180,236 70,237 Z" fill="var(--route-red)"/>
    </svg>

    <div class="front-brand">
      <span class="front-brand__dot"></span>
      <span class="front-brand__name">Prairie Lantern Popcorn</span>
    </div>

    <div class="person">
      <p class="person__name">Dale Whitcombe</p>
      <p class="person__title">Founder/President</p>
    </div>

    <p class="tagline">"<strong>POP</strong>ular for a reason"</p>

    <ul class="contacts">
      <li>+1 555 308 4726
        <svg viewBox="0 0 12 12"><path d="M1,4 C1,2 3,1 6,1 C9,1 11,2 11,4 L8.5,4.5 L8,3 L4,3 L3.5,4.5 Z M3,6 L9,6 L10,11 L2,11 Z"/></svg>
      </li>
      <li>prairielanternpopcorn.com
        <svg viewBox="0 0 12 12"><path d="M1,3 L11,3 L11,10 L1,10 Z M1.5,3.5 L6,7 L10.5,3.5" stroke="#141416" stroke-width="1"/></svg>
      </li>
      <li>Dale@prairielanternpopcorn.com
        <svg viewBox="0 0 12 12"><circle cx="6" cy="6" r="5"/></svg>
      </li>
    </ul>
  </section>

</body>
</html>
```